MV Decor

There is a sample provided with the arabic text of the business card. please copy paste the same text and the same Logo (The two triangles) Just try to incorproate the Brown background attached (you are free to change the colors) Id like the colors to be mainly shades of black and red.

```html
<!DOCTYPE html>
<html lang="ar">
<head>
<meta charset="utf-8">
<title>MV Decor – Business Card</title>
<link rel="stylesheet" href="https://fonts.googleapis.com/css2?family=Aref+Ruqaa:wght@400;700&family=Tajawal:wght@400;500&family=Roboto:wght@400&display=swap">
<style>
  :root {
    --backdrop: #4a3020;
    --card-red: #cf1f40;
    --card-red-light: #e1354f;
    --card-red-deep: #c41a3a;
    --ink-dark: #25241f;
    --text-white: #ffffff;
    --rule: rgba(255,255,255,0.8);
  }
  * { box-sizing: border-box; margin: 0; padding: 0; }
  html, body { width: 1125px; height: 1200px; overflow: hidden; }
  body { background: var(--backdrop); position: relative; font-family: "Tajawal", sans-serif; color: var(--text-white); }

  .card {
    position: absolute;
    left: 171px;
    width: 826px;
    height: 472px;
    overflow: hidden;
    box-shadow: 0 4px 10px rgba(0,0,0,0.45);
  }
  .card--front { top: 106px; }
  .card--back { top: 639px; }

  .card__surface {
    position: absolute; inset: 0;
    background: linear-gradient(90deg, var(--card-red-deep), var(--card-red-light) 30%, var(--card-red) 55%, var(--card-red-light) 80%, var(--card-red-deep));
  }
  .card__band {
    position: absolute; left: 0; right: 0; bottom: 0; height: 18px;
    background: var(--ink-dark);
  }

  .brand {
    position: absolute;
    display: flex; align-items: center; gap: 12px;
    font-family: "Tajawal", sans-serif;
    font-weight: 500;
    color: var(--text-white);
    letter-spacing: 1px;
    white-space: nowrap;
  }
  .brand__square { display: block; background: var(--text-white); }
  .card--front .brand { left: 244px; top: 212px; transform: translateX(-50%); font-size: 46px; }
  .card--front .brand__square { width: 22px; height: 22px; }
  .card--back .brand { left: 249px; top: 238px; transform: translate(-50%, -50%); font-size: 58px; }
  .card--back .brand__square { width: 28px; height: 28px; }

  .divider {
    position: absolute; left: 396px; top: 95px; width: 1px; height: 253px;
    background: var(--rule);
  }

  .profile {
    position: absolute; right: 149px; top: 100px; width: 260px;
    direction: rtl; text-align: right;
  }
  .profile__name {
    font-family: "Aref Ruqaa", serif; font-weight: 700;
    font-size: 24px; line-height: 1.2; white-space: nowrap;
  }
  .profile__role {
    font-family: "Aref Ruqaa", serif; font-weight: 400;
    font-size: 17px; line-height: 1.2; margin: 4px 40px 0 0;
  }
  .profile__credentials {
    list-style: none; margin-top: 20px;
    font-size: 20px; line-height: 26.5px;
  }
  .profile__phone {
    display: flex; align-items: center; gap: 6px;
    direction: ltr; justify-content: flex-end;
    font-family: "Roboto", sans-serif; font-size: 20px;
    margin-top: 21px; margin-right: 6px;
  }
  .profile__phone svg { width: 18px; height: 18px; }

  .credential-list {
    position: absolute; right: 115px; top: 106px;
    list-style: none; direction: rtl;
    font-size: 24px; line-height: 33px;
  }
  .credential-list li { display: flex; align-items: center; }
  .credential-list li::after {
    content: ""; width: 8px; height: 8px; border-radius: 50%;
    background: var(--text-white); margin-right: 9px;
  }
</style>
</head>
<body>

  <section class="card card--front" aria-label="Business card front">
    <div class="card__surface" role="img" aria-label="Red vertical stripe pattern background"></div>
    <div class="brand"><span class="brand__square"></span>MV DECOR</div>
    <div class="divider"></div>
    <div class="profile">
      <p class="profile__name">المهندس / سالم يوسف الراشد</p>
      <p class="profile__role">أستاذ جامعي</p>
      <ul class="profile__credentials">
        <li>ماجستير هندسة ديكور</li>
        <li>دبلوم عالي فن تشكيلي</li>
        <li>أكاديمية النخبة (باريس)</li>
        <li>استشارات هندسية-فنية</li>
      </ul>
      <p class="profile__phone">
        <svg viewBox="0 0 24 24" aria-hidden="true"><path fill="#fff" d="M6.6 10.8a15.1 15.1 0 0 0 6.6 6.6l2.2-2.2c.3-.3.7-.4 1-.2 1.1.4 2.3.6 3.6.6.6 0 1 .4 1 1V20c0 .6-.4 1-1 1A17 17 0 0 1 3 4c0-.6.4-1 1-1h3.5c.6 0 1 .4 1 1 0 1.3.2 2.5.6 3.6.1.3 0 .7-.2 1z"/></svg>
        <span>35550142 / 65550198</span>
      </p>
    </div>
    <div class="card__band"></div>
  </section>

  <section class="card card--back" aria-label="Business card back">
    <div class="card__surface" role="img" aria-label="Red vertical stripe pattern background"></div>
    <div class="brand"><span class="brand__square"></span>MV DECOR</div>
    <ul class="credential-list">
      <li>ماجستير هندسة ديكور</li>
      <li>دبلوم عالي فن تشكيلي</li>
      <li>أكاديمية النخبة (باريس)</li>
      <li>استشارات هندسية-فنية</li>
      <li>ماجستير هندسة ديكور</li>
      <li>دبلوم عالي فن تشكيلي</li>
      <li>أكاديمية النخبة (باريس)</li>
      <li>استشارات هندسية-فنية</li>
    </ul>
  </section>

</body>
</html>
```